PowerPoint Design Project

Powerpoint design for an online marketing agency.
PP will be used as a WhitePaper to showcase our expertise.
Our USP is that we use data for marketing so the design must reflect this with charts and graphs.
A set of images is available in our pictovault account
http://www.pictovault.example/photos/torqlane/sets/48302917564820193/with/3816492057/
We already have written real content for the PP for you to work with.
Updates

1. I have added a sample of the content a 2-page extract in a word document. The full document is around 15 pages.
2. While the finished piece is to be in PowerPoint format, it will also be used as a White Paper so the design should reflect this - i.e it should be able to be read like it was a well designed Word document not just a PP
3. The design you see in the sample 2-page document is just for illustration purposes it is not intended to influence the final design at all. So for example it currently has some pull-quotes in black boxes - that is just to show what they are and I don't want the final piece to have black boxes around quotes.
4. I've been asked to make this project guaranteed: as this is the first time I've used CraftHive I'm going to keep it as a standard project but we are committed to the work.
5. The current deadline is for the START of design work. We need the completed design by 21 September, so there is plenty of time to schedule this in with your other work.
Many thanks
Owen 

The designs shown so far would not be suitable for turning into a WhitePaper. For example the bars across the top of the design create a break at the start of each page rather than emphasise the continuous nature of the document. 

Here is an example of some great design for a similar project - and we've uploaded another sample as a file

http://www.zephyrmkt.example/downloads/[ZEPHYR]-what-its-like-working-

If you asked me for some ideas on the feel of the design I would say:

1. Bold - it has to look interesting - corporate world but it doesn't need to feel dull/grey
2. Exciting 
3. Precise - easy to read , not a fussy design

Target Market(s)

Business developers, sales managers, CEOs of companies with over 5 employees but without their own marketing department

Industry/Entity Type

Marketing

Requirements
Must have
• Flawless design that says "this company is smart and means business"
Nice to have
• the powerpoint should lend itself to easy file/saveas to be delivered as a PDF and for individual slides to be extracted for presentation, or use as images in blog posts etc (so for example any page number must be easy to remove).
Should not have
• no cartoons, no line drawings, nothing to obscure easy legibility

```html
<!DOCTYPE html>
<html lang="en">
<head>
<meta charset="utf-8">
<title>Thought Leadership Drives Views</title>
<link rel="stylesheet" href="https://fonts.googleapis.com/css2?family=Oswald:wght@500;700&family=Open+Sans:wght@400;600&display=swap">
<style>
  :root {
    --navy: #0b2a66;
    --royal: #1d56a0;
    --sky: #7aa6d8;
    --panel: #ffffff;
    --callout: #0d5cae;
    --callout-edge: #0a2f63;
    --ink: #1a1a1a;
    --muted: #7a7f88;
    --footer-top: #e9f0f7;
    --footer-bottom: #b9cde3;
    --badge-ring: #1d56a0;
  }
  * { margin: 0; padding: 0; box-sizing: border-box; }
  html, body { width: 1200px; height: 900px; overflow: hidden; background: #fff; }
  .slide {
    position: relative;
    width: 1200px; height: 900px;
    background: linear-gradient(180deg, #ffffff 0%, #f5f7fa 20%, #ffffff 40%, #ffffff 85%);
    font-family: "Open Sans", Arial, sans-serif;
    overflow: hidden;
  }
  .header-accent {
    position: absolute; left: 40px; top: 112px; width: 1120px; height: 4px;
    background: linear-gradient(90deg, var(--navy) 0%, var(--royal) 45%, var(--sky) 75%, rgba(122,166,216,0) 100%);
  }
  .slide-title {
    position: absolute; left: 40px; top: 28px;
    font-family: "Oswald", "Arial Narrow", sans-serif; font-weight: 700;
    font-size: 54px; line-height: 1; color: var(--navy); letter-spacing: 0.5px;
  }
  .brand-name {
    position: absolute; right: 28px; top: 20px;
    font-family: "Oswald", "Arial Narrow", sans-serif; font-weight: 700;
    font-size: 72px; line-height: 1; color: var(--royal);
  }
  .chart-panel {
    position: absolute; left: 55px; top: 172px; width: 915px; height: 593px;
    background: var(--panel);
    box-shadow: 2px 3px 8px rgba(40,60,90,0.35);
  }
  .chart-svg { position: absolute; left: 0; top: 0; }
  .axis-label { font-family: Arial, sans-serif; font-size: 12px; font-weight: 700; fill: var(--ink); }
  .category-label { font-family: Arial, sans-serif; font-size: 12px; font-weight: 700; fill: var(--ink); }
  .callout-text {
    position: absolute; left: 456px; top: 217px; width: 445px;
    color: #fff; font-size: 17.5px; line-height: 1.38;
  }
  .callout-text ul { list-style: none; margin-top: 24px; }
  .callout-source { font-size: 11.5px; margin-top: 16px; }
  .footer-band {
    position: absolute; left: 0; top: 795px; width: 1200px; height: 105px;
    background: linear-gradient(180deg, var(--footer-top) 0%, #ffffff 35%, var(--footer-bottom) 100%);
    border-top: 2px solid #d5e0ec;
  }
  .copyright {
    position: absolute; left: 48px; top: 845px;
    font-family: "Oswald", "Arial Narrow", sans-serif; font-weight: 500;
    font-size: 20px; color: var(--muted);
  }
  .page-number {
    position: absolute; left: 1085px; top: 788px; width: 60px; height: 60px;
    border-radius: 50%; background: #fff; border: 2px solid var(--badge-ring);
    display: flex; align-items: center; justify-content: center;
    font-family: "Oswald", "Arial Narrow", sans-serif; font-weight: 700;
    font-size: 26px; color: var(--navy);
  }
</style>
</head>
<body>
<div class="slide">
  <h1 class="slide-title">Thought Leadership Drives Views</h1>
  <div class="brand-name">torqlane</div>
  <div class="header-accent"></div>

  <div class="chart-panel"></div>

  <svg class="chart-svg" width="1200" height="900" viewBox="0 0 1200 900" aria-label="Bar chart of popular words for attracting views">
    <polygon points="98,735 930,735 955,717 113,717" fill="#ffffff" stroke="#555" stroke-width="1"/>
    <line x1="98" y1="205" x2="98" y2="735" stroke="#555" stroke-width="1"/>
    <g class="y-axis">
      <text class="axis-label" x="84" y="739" text-anchor="end">0</text>
      <text class="axis-label" x="84" y="663" text-anchor="end">100</text>
      <text class="axis-label" x="84" y="587" text-anchor="end">200</text>
      <text class="axis-label" x="84" y="512" text-anchor="end">300</text>
      <text class="axis-label" x="84" y="436" text-anchor="end">400</text>
      <text class="axis-label" x="84" y="360" text-anchor="end">500</text>
      <text class="axis-label" x="84" y="285" text-anchor="end">600</text>
      <text class="axis-label" x="84" y="209" text-anchor="end">700</text>
    </g>

    <g class="bars">
      <rect x="130" y="250" width="33" height="480" fill="#3a5a93"/>
      <polygon points="130,250 139,241 172,241 163,250" fill="#5b7db6"/>
      <polygon points="163,250 172,241 172,721 163,730" fill="#223d6e"/>
      <rect x="213" y="311" width="33" height="419" fill="#a8322e"/>
      <polygon points="213,311 222,302 255,302 246,311" fill="#c8524d"/>
      <polygon points="246,311 255,302 255,721 246,730" fill="#7a1f1c"/>
      <rect x="295" y="557" width="33" height="173" fill="#7d973a"/>
      <polygon points="295,557 304,548 337,548 328,557" fill="#9cb658"/>
      <polygon points="328,557 337,548 337,721 328,730" fill="#5a6f25"/>
      <rect x="370" y="557" width="33" height="173" fill="#65457f"/>
      <polygon points="370,557 379,548 412,548 403,557" fill="#8464a0"/>
      <polygon points="403,557 412,548 412,721 403,730" fill="#462d5c"/>
      <rect x="453" y="557" width="33" height="173" fill="#3a8aa6"/>
      <polygon points="453,557 462,548 495,548 486,557" fill="#5aaac6"/>
      <polygon points="486,557 495,548 495,721 486,730" fill="#25657c"/>
      <rect x="535" y="591" width="33" height="139" fill="#db7228"/>
      <polygon points="535,591 544,582 577,582 568,591" fill="#f0904a"/>
      <polygon points="568,591 577,582 577,721 568,730" fill="#a6521a"/>
      <rect x="618" y="637" width="33" height="93" fill="#8a9ecf"/>
      <polygon points="618,637 627,628 660,628 651,637" fill="#a9bce6"/>
      <polygon points="651,637 660,628 660,721 651,730" fill="#66799f"/>
      <rect x="700" y="637" width="33" height="93" fill="#cf7f7e"/>
      <polygon points="700,637 709,628 742,628 733,637" fill="#e6a09f"/>
      <polygon points="733,637 742,628 742,721 733,730" fill="#a05b5a"/>
      <rect x="785" y="697" width="33" height="33" fill="#b4cc82"/>
      <polygon points="785,697 794,688 827,688 818,697" fill="#cfe3a2"/>
      <polygon points="818,697 827,688 827,721 818,730" fill="#8aa35c"/>
      <rect x="868" y="708" width="33" height="22" fill="#a090c0"/>
      <polygon points="868,708 877,699 910,699 901,708" fill="#bdb0da"/>
      <polygon points="901,708 910,699 910,721 901,730" fill="#776896"/>
    </g>

    <g class="x-axis">
      <text class="category-label" x="147" y="760" text-anchor="middle">insights</text>
      <text class="category-label" x="230" y="760" text-anchor="middle">analysis</text>
      <text class="category-label" x="312" y="760" text-anchor="middle">answers</text>
      <text class="category-label" x="387" y="760" text-anchor="middle">questions</text>
      <text class="category-label" x="470" y="760" text-anchor="middle">advice</text>
      <text class="category-label" x="552" y="760" text-anchor="middle">review</text>
      <text class="category-label" x="635" y="760" text-anchor="middle">why</text>
      <text class="category-label" x="717" y="760" text-anchor="middle">product</text>
      <text class="category-label" x="802" y="760" text-anchor="middle">top</text>
      <text class="category-label" x="885" y="760" text-anchor="middle">best</text>
    </g>

    <polygon points="447,207 912,207 912,437 866,483 447,483" fill="var(--callout)" stroke="var(--callout-edge)" stroke-width="2"/>
    <polygon points="866,483 912,437 876,447" fill="#093f7c" stroke="var(--callout-edge)" stroke-width="2"/>
  </svg>

  <div class="callout-text">
    <p>The most popular words for attracting views to social media content like blogs or calls to action, imply "thought leadership" including phrases like:</p>
    <ul>
      <li>- insights</li>
      <li>- analysis</li>
      <li>- answers</li>
      <li>- questions.</li>
    </ul>
    <p class="callout-source">Source: @kestrelvane,&nbsp; http://www.leadwright.example/the-science-of-blogging/</p>
  </div>

  <div class="footer-band"></div>
  <div class="copyright">Copyright@torqlane</div>
  <div class="page-number">01</div>
</div>
</body>
</html>
```